Meridale Staffing Website

My business has been word of mouth over the last 3 years and has grown. Now I need a website for additional marketing as we have new clients asking for a website.

You have already completed my Logo during an earlier project. I have attached the logo.

We do Staff Augmentation and Operation Support.

What is that?
Staff augmentation is an outsourcing strategy that allows companies to fill specific, temporary roles to achieve business objectives. This staffing method complements existing teams with specific talent, enhancing business capabilities or filling gaps left by members on extended leave.

We work alongside the internal recruiting team to assist clients to meet and exceed financial goals.

```html
<!DOCTYPE html>
<html lang="en">
<head>
<meta charset="utf-8">
<title>Meridale Staffing</title>
<link href="https://fonts.googleapis.com/css2?family=Lato:wght@400;700;900&display=swap" rel="stylesheet">
<style>
:root{
  --navy:#0b3f6b;
  --navy-deep:#08304f;
  --ink:#111418;
  --grey-btn:#6e6e6e;
  --text:#3c3c3c;
  --white:#ffffff;
  --accent:#3b8fd6;
}
*{box-sizing:border-box;margin:0;padding:0}
html,body{width:1200px;height:4505px;overflow:hidden;background:var(--white)}
body{font-family:"Lato",sans-serif;color:var(--text);position:relative}
.page{position:relative;width:1200px;height:4505px;overflow:hidden}
.abs{position:absolute}
/* top bar */
.topbar{top:0;left:0;width:1200px;height:62px;background:var(--white)}
.social{display:flex;gap:22px}
.social span{width:24px;height:24px;border-radius:50%;background:var(--navy);display:block}
.topbar .social{position:absolute;left:72px;top:19px}
.contact-top{position:absolute;right:72px;top:20px;display:flex;gap:24px;font-weight:900;font-size:17px;color:var(--navy)}
.contact-top div{display:flex;align-items:center;gap:10px}
/* hero */
.hero{top:62px;left:0;width:1200px;height:673px;background:linear-gradient(120deg,#5d6770 0%,#8d99a5 35%,#4c5f73 70%,#2f3e4f 100%)}
.brand{position:absolute;left:75px;top:22px;display:flex;align-items:center;gap:12px;color:var(--white);font-weight:900;font-size:26px;line-height:1}
.brand i{width:52px;height:52px;border-radius:50%;background:var(--white);display:block}
.brand small{display:block;font-size:17px;font-weight:900}
.nav{position:absolute;right:90px;top:58px;display:flex;gap:40px;font-size:14px;font-weight:700;color:var(--white);letter-spacing:.3px}
.hero h1{position:absolute;top:220px;width:1200px;text-align:center;color:var(--white);font-weight:900;font-size:62px;letter-spacing:.5px}
.hero p{position:absolute;top:298px;left:150px;width:900px;text-align:center;color:var(--white);font-size:21px;font-weight:700;line-height:31px}
.btn{display:flex;align-items:center;justify-content:center;border-radius:32px;font-weight:900;font-size:20px;color:var(--white)}
.hero .btn{position:absolute;top:378px;left:471px;width:258px;height:62px;background:var(--navy)}
.dots{display:flex;gap:12px}
.dots span{width:10px;height:10px;border-radius:50%;background:var(--white)}
.dots span.on{background:var(--accent)}
.hero .dots{position:absolute;top:605px;left:563px}
.hero-curve{top:620px;left:0}
/* welcome */
.welcome h2{left:75px;top:822px;font-size:50px;font-weight:900;color:var(--navy);line-height:58px}
.welcome p{left:75px;top:958px;width:540px;font-size:15px;line-height:30.5px}
.welcome .btn{left:75px;top:1178px;width:258px;height:63px;background:var(--grey-btn)}
.welcome-photo{left:680px;top:800px;width:400px;height:480px;border-radius:50%;background:radial-gradient(circle at 50% 45%,#35597a,#0b3f6b 60%,#082a46)}
/* services */
.services{top:1340px;left:0;width:1200px;height:1030px}
.services svg.band{position:absolute;top:0;left:0}
.services h2{position:absolute;top:112px;width:1200px;text-align:center;font-size:48px;font-weight:900;color:var(--white)}
.services p{position:absolute;top:188px;left:90px;width:1020px;text-align:center;color:var(--white);font-size:15px;line-height:29px}
.node-label{position:absolute;color:var(--white);font-weight:900;font-size:22px;line-height:29px}
.node-label.right{text-align:right}
.hub-name{position:absolute;left:452px;top:535px;width:296px;text-align:center;color:var(--navy);font-weight:900;font-size:28px;line-height:34px}
/* partners */
.partners h2{top:2405px;width:1200px;text-align:center;font-size:32px;font-weight:900;color:var(--navy)}
.badge{top:2488px;height:56px;border-radius:8px;background:#d9dde2}
.arrow-sm{top:2502px;font-size:26px;color:#c6cad0}
.partners .dots{position:absolute;top:2600px;left:559px}
.partners .dots span{background:#333}
.partners .dots span.on{background:var(--accent)}
/* team */
.team-band{top:2680px;left:0}
.team-photo{left:73px;top:2795px;width:490px;height:490px;border-radius:50%;background:linear-gradient(160deg,#d9d4cc,#9aa3ad 55%,#5a6572)}
.team h2{left:615px;top:2862px;font-size:48px;font-weight:900;color:var(--white)}
.team p{left:617px;top:2935px;width:500px;font-size:15px;line-height:30.5px;color:var(--white)}
.team .btn{left:617px;top:3150px;width:258px;height:63px;background:var(--grey-btn)}
/* news */
.news h2{top:3458px;width:1200px;text-align:center;font-size:48px;font-weight:900;color:var(--navy)}
.card{top:3537px;width:331px}
.card .img{height:218px;border-radius:8px}
.card time{display:block;margin-top:22px;font-size:18px;font-weight:700;color:var(--navy)}
.card h3{margin-top:8px;font-size:22px;line-height:32px;font-weight:700;color:#333}
/* footer */
.footer-shape{top:3960px;left:0}
.footer-mark{left:560px;top:3975px;width:80px;height:80px;border-radius:50%;background:var(--white);border:6px solid var(--navy)}
.fcol{top:4142px;color:var(--white)}
.fcol h4{font-size:22px;font-weight:900;margin-bottom:12px}
.fcol li{list-style:none;font-size:15px;line-height:32.5px}
.fcol .row{display:flex;gap:16px;font-size:14px;line-height:24px;margin-bottom:10px}
.fcol .row svg{flex:none;margin-top:5px}
.fcol .map{font-weight:900;font-size:14px;margin-top:4px}
.rule{left:0;top:4395px;width:1200px;height:1px;background:#3a3d42}
.legal{left:77px;top:4425px;color:var(--white);font-size:13px;line-height:33px}
.footer-social{left:905px;top:4440px}
.footer-social span{background:var(--white)}
</style>
</head>
<body>
<div class="page">

  <header class="abs topbar">
    <div class="social" aria-label="Social links"><span></span><span></span><span></span><span></span><span></span></div>
    <div class="contact-top">
      <div><svg width="14" height="14" viewBox="0 0 24 24"><path d="M6 2l4 4-2 3a12 12 0 007 7l3-2 4 4-3 4C10 22 2 14 2 5z" fill="#0b3f6b"/></svg>1-800-555-0142</div>
      <div><svg width="16" height="12" viewBox="0 0 16 12"><rect width="16" height="12" rx="1" fill="#0b3f6b"/><path d="M1 1l7 5 7-5" stroke="#fff" stroke-width="1.5" fill="none"/></svg>hello@meridalestaffing.com</div>
    </div>
  </header>

  <section class="abs hero" role="img" aria-label="Business professional selecting candidate profiles on a floating screen grid">
    <div class="brand"><i></i><div>MERIDALE<small>STAFFING, LLC</small></div></div>
    <nav class="nav"><span>HOME</span><span>ABOUT US</span><span>SERVICES</span><span>BLOG</span><span>CAREER</span><span>CONTACT US</span></nav>
    <h1>MERIDALE STAFFING, LLC</h1>
    <p>Nemo enim ipsam voluptatem quia voluptas sit aspernatur aut odit aut fugit nostrud exercitation ullamco laboris nisi ut aliquip.</p>
    <div class="btn">Get In Touch</div>
    <div class="dots"><span class="on"></span><span></span><span></span><span></span></div>
  </section>
  <svg class="abs hero-curve" width="1200" height="120" viewBox="0 0 1200 120"><path d="M0 20 Q600 210 1200 20 V120 H0Z" fill="#fff"/></svg>

  <section class="welcome">
    <h2 class="abs">Welcome to<br>Meridale Staffing</h2>
    <p class="abs">Sed ut perspiciatis unde omnis iste natus error sit voluptatem accusantium doloremque laudantium, totam rem aperiam, eaque ipsa quae ab illo inventore veritatis et quasi architecto beatae vitae dicta sunt explicabo. Nemo enim ipsam voluptatem quia voluptas sit aspernatur aut odit aut fugit, sed quia consequuntur magni dolores eos qui ration.</p>
    <div class="abs btn">Read More</div>
    <div class="abs welcome-photo" role="img" aria-label="Team meeting photo in brand navy tones"></div>
  </section>

  <section class="abs services">
    <svg class="band" width="1200" height="1030" viewBox="0 0 1200 1030">
      <defs><linearGradient id="svcBg" x1="0" y1="0" x2="1" y2="1"><stop offset="0" stop-color="#0d426f"/><stop offset="1" stop-color="#072b49"/></linearGradient></defs>
      <path d="M0 60 Q600 -60 1200 105 V915 Q600 1110 0 915Z" fill="url(#svcBg)"/>
      <g stroke="#fff" stroke-width="6">
        <line x1="600" y1="560" x2="388" y2="363"/><line x1="600" y1="560" x2="813" y2="363"/>
        <line x1="600" y1="560" x2="370" y2="565"/><line x1="600" y1="560" x2="295" y2="803"/>
        <line x1="600" y1="560" x2="905" y2="803"/>
      </g>
      <circle cx="600" cy="560" r="148" fill="#fff"/>
      <g fill="#fff"><circle cx="388" cy="363" r="50"/><circle cx="813" cy="363" r="50"/><circle cx="370" cy="565" r="48"/><circle cx="295" cy="803" r="50"/><circle cx="905" cy="803" r="50"/></g>
      <g stroke="#1b2733" stroke-width="2.5" fill="none" stroke-linecap="round">
        <circle cx="388" cy="352" r="11"/><path d="M370 385c2-12 34-12 36 0"/><path d="M398 378l5 5 9-10"/>
        <rect x="793" y="345" width="40" height="28" rx="4"/><path d="M803 373l-6 10 14-10"/><path d="M801 355h24M801 363h16"/>
        <circle cx="370" cy="552" r="9"/><circle cx="354" cy="578" r="6"/><circle cx="386" cy="578" r="6"/><path d="M370 561v8"/>
        <rect x="280" y="785" width="26" height="34" rx="2"/><path d="M286 795h14M286 803h14M286 811h8"/><circle cx="310" cy="790" r="6"/>
        <path d="M885 822h40M890 820v-14M900 820v-22M910 820v-10M920 820v-28"/><circle cx="896" cy="790" r="5"/>
      </g>
    </svg>
    <h2>Staff Augmentation Services</h2>
    <p>Sed ut perspiciatis unde omnis iste natus error sit voluptatem accusantium doloremque laudantium, totam rem aperiam, eaque ipsa quae ab illo inventore veritatis et quasi architecto beatae vitae dicta sunt explicabo.</p>
    <div class="node-label right" style="left:150px;top:334px;width:166px">Background<br>Verification</div>
    <div class="node-label" style="left:884px;top:334px">Feedback<br>Mechanism</div>
    <div class="node-label right" style="left:110px;top:532px;width:188px">Behavioral<br>Development</div>
    <div class="node-label right" style="left:60px;top:772px;width:172px">Handling of<br>Work Project</div>
    <div class="node-label" style="left:973px;top:772px">Performance<br>Management</div>
    <div class="hub-name">Meridale<br>Staffing</div>
  </section>

  <section class="partners">
    <h2 class="abs">Company Partners</h2>
    <div class="abs arrow-sm" style="left:32px">&#8249;</div>
    <div class="abs badge" style="left:64px;width:200px" aria-label="Partner badge"></div>
    <div class="abs badge" style="left:360px;width:192px" aria-label="Partner badge"></div>
    <div class="abs badge" style="left:636px;width:220px" aria-label="Partner badge"></div>
    <div class="abs badge" style="left:968px;width:140px" aria-label="Partner badge"></div>
    <div class="abs arrow-sm" style="left:1152px">&#8250;</div>
    <div class="dots"><span class="on"></span><span></span><span></span><span></span></div>
  </section>

  <svg class="abs team-band" width="1200" height="730" viewBox="0 0 1200 730"><path d="M0 95 Q600 -90 1200 95 V636 Q600 815 0 636Z" fill="#0b3f6b"/></svg>
  <section class="team">
    <div class="abs team-photo" role="img" aria-label="Smiling team of professionals standing in an office"></div>
    <h2 class="abs">Meet Our Team</h2>
    <p class="abs">Sed ut perspiciatis unde omnis iste natus error sit voluptatem accusantium doloremque laudantium, totam rem aperiam, eaque ipsa quae ab illo inventore veritatis et quasi architecto beatae vitae dicta sunt explicabo. Nemo enim ipsam voluptatem quia voluptas sit aspernatur aut odit aut fugit, sed quia consequuntur magni dolores eos qui ration.</p>
    <div class="abs btn">Read More</div>
  </section>

  <section class="news">
    <h2 class="abs">Latest News</h2>
    <article class="abs card" style="left:75px"><div class="img" role="img" aria-label="Colleagues gathered around a laptop" style="background:linear-gradient(135deg,#c9cdd2,#6f7c88)"></div><time>Jan 12, 2022</time><h3>Sed ut perspiciatis unde omnis iste natus error sit voluptatem accusantium dolore.</h3></article>
    <article class="abs card" style="left:435px"><div class="img" role="img" aria-label="Team discussing documents at a table" style="background:linear-gradient(135deg,#e2dcd3,#8a8f86)"></div><time>Jan 12, 2022</time><h3>Sed ut perspiciatis unde omnis iste natus error sit voluptatem accusantium dolore.</h3></article>
    <article class="abs card" style="left:795px"><div class="img" role="img" aria-label="Business handshake in a meeting room" style="background:linear-gradient(135deg,#b9c3cc,#3c4a5a)"></div><time>Jan 12, 2022</time><h3>Sed ut perspiciatis unde omnis iste natus error sit voluptatem accusantium dolore.</h3></article>
  </section>

  <svg class="abs footer-shape" width="1200" height="545" viewBox="0 0 1200 545">
    <path d="M0 150 Q600 -10 1200 150" stroke="#0b3f6b" stroke-width="14" fill="none"/>
    <path d="M0 175 Q600 20 1200 175 V545 H0Z" fill="#111418"/>
  </svg>
  <div class="abs footer-mark" aria-label="Meridale Staffing"></div>
  <footer>
    <div class="abs fcol" style="left:75px"><h4>Company</h4><ul><li>Home</li><li>About Us</li><li>Services</li><li>Blog</li><li>Career</li><li>Contact Us</li></ul></div>
    <div class="abs fcol" style="left:317px"><h4>Services</h4><ul><li>Sed ut perspiciatis</li><li>Unde omnis iste</li><li>Natus error sit volupt</li><li>Accusantium</li><li>Doloremque</li></ul></div>
    <div class="abs fcol" style="left:609px"><h4>Resources</h4><ul><li>Sed ut perspiciatis</li><li>Unde omnis iste</li><li>Natus error sit volupt</li><li>Accusantium</li><li>Doloremque</li></ul></div>
    <div class="abs fcol" style="left:887px"><h4>Contact Us</h4>
      <div class="row"><svg width="12" height="16" viewBox="0 0 12 16"><path d="M6 0a6 6 0 016 6c0 4-6 10-6 10S0 10 0 6a6 6 0 016-6z" fill="#fff"/><circle cx="6" cy="6" r="2" fill="#111418"/></svg><span>42 Alder Court, Fenwick,<br>Surrey RH9 2LT</span></div>
      <div class="row"><svg width="12" height="12" viewBox="0 0 24 24"><path d="M6 2l4 4-2 3a12 12 0 007 7l3-2 4 4-3 4C10 22 2 14 2 5z" fill="#fff"/></svg><span>1-800-555-0142</span></div>
      <div class="row"><svg width="14" height="10" viewBox="0 0 16 12"><rect width="16" height="12" rx="1" fill="#fff"/><path d="M1 1l7 5 7-5" stroke="#111418" stroke-width="1.5" fill="none"/></svg><span>hello@meridalestaffing.com</span></div>
      <div class="map">Map Location</div>
    </div>
    <div class="abs rule"></div>
    <div class="abs legal">Copyright © 2022. Meridale Staffing. All Right Reserved<br>Privacy Policy &nbsp;&nbsp;/&nbsp;&nbsp; Terms &amp; Conditions</div>
    <div class="abs social footer-social" aria-label="Social links"><span></span><span></span><span></span><span></span><span></span></div>
  </footer>

</div>
</body>
</html>
```